Velmora Consulting Business

** Please add the content information from my old business card
1. I would like to see a two sided business card with both options with the 1st Option--Tallow Spire-new WHITE BACKGROUND LOGO
2 nd Option-Tallow Spire - new BLACK- Background Logo
3rd -Option a business card with my Photo on the card
Please add the new word to the card information:
EXECUTION
AS THE OWNER'S REP
WE AIM TO ACHIEVE YOUR
INFRASTRUCTURE VISION with
OUR SPECIALIZATION & EXECUTION in:

FUNDING Planning
BUSINESS Planning
INFRASTRUCTURE Planning
PROJECT Management
Since 2012
_____________________________________________________________________
I want to get spot uv raised printing. I was liking a a nice rich white linen paper stock with black writing & NOT A COLORED CARD other than a variety of white or black cards concept

```html
<!DOCTYPE html>
<html lang="en">
<head>
<meta charset="utf-8">
<title>Velmora Consulting — Business Cards</title>
<link rel="stylesheet" href="https://fonts.googleapis.com/css2?family=Montserrat:wght@400;500;600;700&display=swap">
<style>
  :root {
    --stage: #333333;
    --ink: #000000;
    --paper: #ffffff;
    --accent: #e8193c;
    --font: "Montserrat", sans-serif;
  }
  * { box-sizing: border-box; margin: 0; padding: 0; }
  html, body { width: 1200px; height: 1200px; overflow: hidden; }
  body { background: var(--stage); font-family: var(--font); position: relative; }

  .card {
    position: absolute; left: 200px; width: 800px; height: 456px;
    background: var(--ink); overflow: hidden;
    box-shadow: 0 22px 30px -18px rgba(0,0,0,.75);
  }
  .card--back { top: 108px; }
  .card--front { top: 636px; }

  .card__panel { position: absolute; left: 0; top: 0; bottom: 0; background: var(--paper); }
  .card--back .card__panel { width: 330px; }
  .card--front .card__panel { width: 268px; }

  .wordmark {
    position: absolute; transform: translate(-50%, -50%);
    display: flex; align-items: center; gap: 8px;
    color: var(--ink); font-weight: 700; white-space: nowrap;
  }
  .wordmark__dot { width: 10px; height: 10px; background: var(--accent); }
  .card--back .wordmark { left: 166px; top: 290px; font-size: 24px; }
  .card--front .wordmark { left: 134px; top: 330px; font-size: 20px; }

  .accent-bar { position: absolute; left: 320px; top: 82px; width: 22px; height: 292px; background: var(--accent); }

  .pitch { position: absolute; left: 382px; top: 118px; color: var(--paper); }
  .pitch__title { font-size: 24px; font-weight: 700; letter-spacing: .5px; margin-bottom: 12px; }
  .pitch__lead { font-size: 14.5px; font-weight: 500; line-height: 17.6px; margin-bottom: 6px; }
  .pitch__lead b { font-weight: 700; }
  .services { list-style: none; }
  .services li { font-size: 19px; line-height: 25px; font-weight: 500; letter-spacing: .3px; }
  .services .tag { font-weight: 700; padding: 0 3px; margin-right: 3px; }
  .tag--red { background: var(--accent); color: var(--paper); }
  .tag--white { background: var(--paper); color: var(--ink); }
  .pitch__since { font-size: 15px; font-weight: 700; margin-top: 8px; }

  .name-band {
    position: absolute; left: 251px; right: 0; top: 146px; height: 42px;
    background: var(--accent); color: var(--paper);
    font-size: 29px; font-weight: 600; line-height: 42px; padding-left: 37px;
  }
  .contact { position: absolute; left: 288px; top: 196px; color: var(--paper); }
  .contact__role { color: var(--accent); font-size: 16px; font-weight: 500; letter-spacing: 1.5px; margin-bottom: 16px; }
  .contact__line { font-size: 21px; font-weight: 500; line-height: 27.5px; }
  .contact__key { color: var(--accent); }
  .contact__web { color: var(--accent); font-weight: 600; }
  .contact__cities { font-size: 17px; margin-top: 14px; }
  .contact__sep { margin: 0 10px; }
</style>
</head>
<body>
  <section class="card card--back">
    <div class="card__panel">
      <div class="wordmark"><span class="wordmark__dot"></span>Velmora Consulting</div>
    </div>
    <div class="accent-bar"></div>
    <div class="pitch">
      <h2 class="pitch__title">EXECUTION</h2>
      <p class="pitch__lead">AS THE <b>OWNER'S REP</b><br>WE AIM TO ACHIEVE YOUR<br>INFRASTRUCTURE VISION with<br>OUR SPECIALIZATION &amp; EXECUTION in:</p>
      <ul class="services">
        <li><span class="tag tag--red">FUNDING</span>Planning</li>
        <li><span class="tag tag--white">BUSINESS</span>Planning</li>
        <li><span class="tag tag--red">INFRASTRUCTURE</span>Planning</li>
        <li><span class="tag tag--white">PROJECT</span>Management</li>
      </ul>
      <p class="pitch__since">Since 2012</p>
    </div>
  </section>

  <section class="card card--front">
    <div class="card__panel">
      <div class="wordmark"><span class="wordmark__dot"></span>Velmora Consulting</div>
    </div>
    <div class="name-band">Dana Whitcombe-Rourke</div>
    <div class="contact">
      <p class="contact__role">CEO / LEAD PROJECT MANAGER</p>
      <p class="contact__line"><span class="contact__key">C</span> 867.555.0182</p>
      <p class="contact__line"><span class="contact__key">E</span> dana@velmora.ca</p>
      <p class="contact__line contact__web">www.velmora.ca</p>
      <p class="contact__cities">Northgate NT<span class="contact__sep">·</span>Alderbrook NB</p>
    </div>
  </section>
</body>
</html>
```